dsadasdasdasdsa

Industry/Entity Type

Mortgage Broking

Requirements
Must have
• Call-to-action button somewhere on the graphic
Nice to have
• The font of our logo is Montserrat

```html
<!DOCTYPE html>
<html lang="en">
<head>
<meta charset="UTF-8">
<title>Mortgage Broker Directory Banner</title>
<link rel="stylesheet" href="https://fonts.googleapis.com/css2?family=Montserrat:wght@600;700;800;900&display=swap">
<style>
  :root {
    --green-deep: #0f5a32;
    --green-mid: #1f8a4c;
    --green-glow: #2a9d58;
    --panel-white: #ffffff;
    --panel-mint: #c9ecd3;
    --headline-green: #1d5a35;
    --accent-red: #c0392b;
    --button-red: #c22f1f;
    --button-yellow: #ffec1f;
    --mascot-green: #4caf50;
    --mascot-brown: #8a5a2b;
  }
  * { margin: 0; padding: 0; box-sizing: border-box; }
  html, body { width: 1200px; height: 180px; overflow: hidden; }
  body { font-family: "Montserrat", sans-serif; }

  .banner {
    position: relative;
    width: 1200px;
    height: 180px;
    overflow: hidden;
    background: radial-gradient(ellipse at 50% 50%, var(--green-glow) 0%, var(--green-mid) 45%, var(--green-deep) 100%);
  }

  .panel {
    position: absolute;
    left: 32px;
    top: 21px;
    width: 1131px;
    height: 133px;
    border-radius: 20px;
    background: linear-gradient(90deg, var(--panel-white) 0%, var(--panel-white) 40%, var(--panel-mint) 100%);
  }

  .cta-button {
    position: absolute;
    left: 60px;
    top: 71px;
    width: 175px;
    height: 38px;
    border-radius: 19px;
    background: var(--button-red);
    color: var(--button-yellow);
    font-weight: 800;
    font-size: 17px;
    letter-spacing: 0.2px;
    display: flex;
    align-items: center;
    justify-content: center;
    text-decoration: none;
  }

  .mascot {
    position: absolute;
    left: 272px;
    top: 0;
    width: 200px;
    height: 180px;
    border-radius: 80px 80px 40px 40px;
    background: radial-gradient(ellipse at 40% 30%, var(--mascot-green) 0%, #3f8f45 45%, var(--mascot-brown) 100%);
    opacity: 0.9;
  }

  .message {
    position: absolute;
    left: 485px;
    top: 30px;
  }
  .message-lead {
    color: var(--accent-red);
    font-weight: 600;
    font-size: 29px;
    line-height: 36px;
  }
  .message-headline {
    margin-top: 2px;
    color: var(--headline-green);
    font-weight: 900;
    font-size: 36px;
    line-height: 36px;
    text-transform: uppercase;
    letter-spacing: 0;
  }
</style>
</head>
<body>
  <div class="banner">
    <div class="panel"></div>
    <a class="cta-button" href="#">CLICK HERE</a>
    <div class="mascot" role="img" aria-label="Cartoon turtle mascot holding a small house"></div>
    <div class="message">
      <p class="message-lead">Need a Mortgage Broker?</p>
      <h1 class="message-headline">Search now on Australia’s<br>largest directory</h1>
    </div>
  </div>
</body>
</html>
```